Business Cards for new orthopaedic surgery practice

My husband and I are starting our own orthopaedic surgery practice. We are looking for a business card that is uniform, but one will have my name/title and the other will have his. You can just create one design with my name on it for now. But when I choose your design as the winning design I will ask that you add another copy with his name/title.

We are looking for classy, simple, elite all in one. We like dark blues/a little gold/yellow. Something that goes with our logo. We want our logo incorporated. Here is all the info you need:
Business name: RV Bone & Vitality Center
Location: 38517 North Willowmere Ave
Palm Crest, FL 33480
Phone: 954-218-4063
Fax: 954-582-7341
Email: info@myrvbonecare.example

Names: Lydia Vance, M.D.
Board Certified Hand and Upper Extremity Surgeon

Ebo Dansu, M.D.
Board Certified Hip & Knee Replacement/General Orthopaedic Surgeon

Can decide what you want to put on the back. Maybe a slogan:
Grounded in Care. Centered on You

I am just going to upload our logo. The only thing is if we select you as the winning design, the location, and phone numbers may change. We will need your help to update that once fully solidified.

Industry/Entity Type

Medical

Contact Information for Business Card

Colors
0054AA
0677BA
7BADD7
CADEEF
E8F1F8
0094D4
00A9DD
6FCCEA
C7EBF8
E9F6FB

Requirements
Must have
• class, appeal,
Should not have
• We want to air on the side of masculine if we are looking at masculine vs. feminine feel. But we still want it classy, sophisticated, and something we will love

```html
<!DOCTYPE html>
<html lang="en">
<head>
<meta charset="utf-8">
<title>RV Bone &amp; Vitality Center — Business Card</title>
<link rel="stylesheet" href="https://fonts.googleapis.com/css2?family=Montserrat:wght@300;400;500;600&display=swap">
<style>
  :root {
    --stage: #e3e3e3;
    --front-bg: #fff4f4;
    --back-bg: #ffffff;
    --navy: #1e3a84;
    --cyan: #00b4dc;
    --ink: #2b2b2b;
    --grey: #4a4a4a;
    --violet: #5b5f9e;
  }
  * { box-sizing: border-box; margin: 0; padding: 0; }
  html, body { width: 1200px; height: 1200px; overflow: hidden; }
  body {
    background: var(--stage);
    font-family: "Montserrat", Arial, sans-serif;
    position: relative;
  }
  .card {
    position: absolute;
    left: 179px;
    width: 861px;
    height: 496px;
  }
  .card--front { top: 84px; background: var(--front-bg); }
  .card--back { top: 621px; background: var(--back-bg); }

  .brand {
    position: absolute;
    left: 0; right: 0; top: 218px;
    display: flex; align-items: center; justify-content: center; gap: 16px;
  }
  .brand__dot {
    width: 36px; height: 36px; border-radius: 50%;
    background: var(--navy);
  }
  .brand__name {
    color: var(--navy);
    font-weight: 600;
    font-size: 36px;
    letter-spacing: 0.5px;
  }
  .tagline {
    position: absolute;
    left: 0; right: 0; top: 332px;
    text-align: center;
    color: var(--cyan);
    font-weight: 500;
    font-size: 32px;
  }

  .practice {
    position: absolute; left: 36px; top: 30px;
    font-size: 31px; font-weight: 600; color: var(--ink);
    letter-spacing: 1px;
  }
  .rule {
    position: absolute; left: 36px; right: 38px; top: 79px;
    height: 3px; background: var(--cyan);
  }
  .doctor {
    position: absolute; left: 36px; top: 94px;
    font-size: 28px; font-weight: 600; color: var(--ink);
  }
  .specialty {
    position: absolute; right: 38px; top: 90px;
    text-align: left;
    font-size: 25px; font-weight: 400; line-height: 32px;
    color: var(--violet);
  }
  .contact {
    position: absolute; left: 36px; top: 358px;
    list-style: none;
  }
  .contact li { height: 38.5px; white-space: nowrap; }
  .contact__label { color: var(--navy); font-size: 25px; font-weight: 500; margin-right: 6px; }
  .contact__value { color: var(--grey); font-size: 22px; font-weight: 400; letter-spacing: 0.5px; }
  .address {
    position: absolute; right: 38px; top: 410px;
    text-align: right; font-style: normal;
    color: var(--grey); font-size: 22px; line-height: 32px; letter-spacing: 0.3px;
  }
</style>
</head>
<body>
  <section class="card card--front">
    <div class="brand">
      <span class="brand__dot"></span>
      <span class="brand__name">RV Bone &amp; Vitality Center</span>
    </div>
    <p class="tagline">Grounded in Care. Centered on You</p>
  </section>

  <section class="card card--back">
    <h1 class="practice">RV Orthopaedic Associates</h1>
    <div class="rule"></div>
    <h2 class="doctor">Lydia Vance, M.D.</h2>
    <p class="specialty">Board Certified Hand and<br>Upper Extremity Surgeon</p>
    <ul class="contact">
      <li><span class="contact__label">Phone.</span> <span class="contact__value">954-218-4063</span></li>
      <li><span class="contact__label">Fax.</span><span class="contact__value">954-582-7341</span></li>
      <li><span class="contact__label">Email.</span><span class="contact__value">info@myrvbonecare.example</span></li>
    </ul>
    <address class="address">38517 North Willowmere Ave<br>Palm Crest, FL 33480</address>
  </section>
</body>
</html>
```